Used Semi Truck Website Redesign

We are redoing the website backend and would like to also do a front end redesign. I would like a Mobile and Desktop mockup for each page. The website has more mobile visitors than desktop visitors. Our competitor is http://www.haulwaybazaar.example. We don't want to copy them exactly but we want a site that looks more like that. We need the functionality of that site. One big difference is that we also sell parts and trailers.

We need a redesign for front page, product detail page, search result page, content page. It is very important that the site is very easy to use on mobile devices. Our target audience is Truck drivers.

Feel free to use demo fonts stock images, and icons. We will purchase necessary 3rd party media when a winner is chosen.

Target Market(s)

People who want to buy used trucks.

Coding

Coded - Design and coding required

Number of Pages Required

5+ page

Requirements
Must have
• Mockup for Desktop and Mobile pages.

```html
<!DOCTYPE html>
<html lang="en">
<head>
<meta charset="utf-8">
<title>Haulway Bazaar – Trucks and Trailers For Sale</title>
<link href="https://fonts.googleapis.com/css2?family=Roboto:wght@300;400;500;700&display=swap" rel="stylesheet">
<style>
:root{
  --navy:#0a2d8c;
  --blue:#0a37a6;
  --btn:#0b2f9e;
  --orange:#f7931e;
  --heavy:#f07a1c;
  --medium:#1d5bd6;
  --light:#2fae3a;
  --trailer:#b0583a;
  --panel:#f5f5f5;
  --line:#e3e3e3;
  --text:#222;
  --muted:#666;
  --footer:#0a33a0;
  --footer-dark:#082a82;
}
*{box-sizing:border-box;margin:0;padding:0}
html,body{width:1200px;height:2406px;overflow:hidden}
body{font-family:"Roboto",Arial,sans-serif;color:var(--text);background:#fff;position:relative}
ul{list-style:none}
a{color:inherit;text-decoration:none}

.topbar{position:absolute;left:0;top:0;width:1200px;height:35px;background:var(--navy);color:#fff;font-size:12px}
.topbar .count{position:absolute;left:88px;top:11px}
.topbar .account{position:absolute;right:90px;top:11px;word-spacing:2px}

.header{position:absolute;top:35px;left:0;width:1200px;height:58px;background:#fff}
.brand{position:absolute;left:88px;top:13px;font-size:27px;font-weight:400;color:#333}
.mainnav{position:absolute;left:845px;top:21px;font-size:13px;display:flex;gap:22px}
.social{position:absolute;left:1001px;top:17px;display:flex;gap:5px}
.social span{width:22px;height:22px;border-radius:50%;display:block}

.search{position:absolute;top:93px;left:0;width:1200px;height:93px;background:var(--blue)}
.search label{position:absolute;left:88px;top:20px;color:#fff;font-size:12px}
.field{position:absolute;top:35px;height:34px;background:#fff;font-size:10px;color:#888;padding:11px 10px}
.field.select::after{content:"";position:absolute;right:10px;top:15px;border:4px solid transparent;border-top-color:#555}
.search-btn{position:absolute;left:1014px;top:35px;width:96px;height:34px;background:var(--orange);color:#fff;font-size:12px;text-align:center;line-height:34px}

.category{position:absolute;left:0;width:746px;height:329px;background:var(--panel)}
.category h2{position:absolute;left:88px;top:34px;font-size:20px;font-weight:400}
.category .sub{position:absolute;left:88px;top:60px;font-size:13px;color:var(--muted)}
.category ul{position:absolute;left:88px;top:96px;font-size:11px;color:#444}
.category li{height:22.4px;padding-left:12px;position:relative}
.category li::before{content:"";position:absolute;left:0;top:5px;width:4px;height:4px;border-radius:50%;background:var(--blue)}
.category .see-all{position:absolute;left:88px;top:258px;width:193px;height:32px;background:var(--btn);color:#fff;font-size:12px;line-height:32px;text-align:center}
.types{position:absolute;left:433px;top:51px;width:268px;height:225px}
.type{position:absolute;width:125px;height:103px;background:#fff;border:1px solid var(--line);border-radius:6px;text-align:center;font-size:11px;color:#888;line-height:1.25}
.type svg{display:block;margin:20px auto 10px;width:50px;height:30px}
.type:nth-child(1){left:0;top:0}.type:nth-child(2){left:143px;top:0}
.type:nth-child(3){left:0;top:120px}.type:nth-child(4){left:143px;top:120px}
.types .hub{position:absolute;left:122px;top:99px;width:24px;height:24px;border-radius:50%;background:#e6e6e6;border:4px solid var(--panel)}
.heavy .type{color:#888}.heavy svg{color:var(--heavy)}
.medium svg{color:var(--medium)}
.light svg{color:var(--light)}
.trailers svg{color:var(--trailer)}

.box{position:absolute;left:770px;width:340px;background:#fff;border:1px solid var(--line)}
.box h3{font-size:15px;font-weight:400;position:absolute;left:21px}
.cols{position:absolute;left:21px;display:grid;grid-template-columns:151px 151px;font-size:10.5px;color:#444}
.cols li{height:22.3px;padding-left:11px;position:relative}
.cols li::before{content:"";position:absolute;left:0;top:5px;width:3px;height:3px;border-radius:50%;background:var(--blue)}
.divider{position:absolute;left:0;right:0;height:1px;background:var(--line)}

.ad{position:absolute;left:770px;top:1123px;width:340px;height:176px;background:linear-gradient(180deg,#3b4450 0%,#1f252d 55%,#14181e 100%);color:#fff;font-size:19px;font-weight:500;display:flex;align-items:center;justify-content:center}

.dealer h3{top:34px;font-size:19px}
.dealer p{position:absolute;left:26px;top:66px;width:150px;font-size:11px;color:#888;line-height:1.6}
.dealer .btn{position:absolute;left:26px;top:130px;width:124px;height:33px;background:var(--btn);color:#fff;font-size:12px;line-height:33px;text-align:center}
.dealer .map{position:absolute;left:191px;top:72px;width:130px;height:76px}

.featured-title{position:absolute;top:1604px;left:0;width:1200px;text-align:center}
.featured-title h2{font-size:20px;font-weight:400}
.featured-title p{font-size:12px;color:var(--muted);margin-top:4px}
.featured-title hr{width:50px;border:0;border-top:1px solid #ccc;margin:10px auto 0}
.card{position:absolute;top:1684px;width:239px;height:308px;border:1px solid var(--line);background:#fff}
.card .photo{height:184px}
.card h4{font-size:15px;font-weight:400;margin:19px 0 0 15px}
.card .model{font-size:11px;color:var(--orange);margin:3px 0 0 15px}
.card ul{margin:4px 0 0 15px;font-size:10.5px;color:#555}
.card li{padding-left:10px;position:relative;line-height:16px}
.card li::before{content:"";position:absolute;left:0;top:7px;width:3px;height:3px;border-radius:50%;background:#555}
.all-featured{position:absolute;left:428px;top:2005px;width:344px;height:35px;background:var(--btn);color:#fff;font-size:13px;line-height:35px;text-align:center}

.footer{position:absolute;top:2085px;left:0;width:1200px;height:276px;background:var(--footer);color:#fff}
.footer h3{position:absolute;top:40px;font-size:17px;font-weight:400}
.post{position:absolute;left:88px;width:290px;height:62px}
.post .thumb{position:absolute;left:0;top:0;width:62px;height:58px;background:linear-gradient(180deg,#9fb3c9,#5a6b80)}
.post .body{position:absolute;left:72px;top:0;font-size:12px;line-height:1.3}
.post .date{color:var(--orange);font-size:10px;margin:2px 0}
.post .text{font-size:11px}
.tweet{position:absolute;left:433px;width:280px}
.tweet .icon{position:absolute;left:0;top:0;width:37px;height:37px;background:#1da1f2}
.tweet .body{position:absolute;left:56px;top:0;font-size:12px;line-height:1.3;width:240px}
.tweet .body .text{font-size:11px}
.tweet .actions{position:absolute;left:0;top:50px;font-size:11px;white-space:nowrap}
.tweet .actions .fav{margin-left:14px}
.tweet .actions .hot{color:var(--orange)}
.links{position:absolute;left:845px;top:71px;display:grid;grid-template-columns:120px 120px;font-size:11px;font-weight:500;row-gap:6px}
.bottombar{position:absolute;top:2361px;left:0;width:1200px;height:45px;background:var(--footer-dark);color:#fff;font-size:12px;text-align:center;line-height:45px}
</style>
</head>
<body>

<svg width="0" height="0" style="position:absolute">
  <defs>
    <symbol id="ico-tractor" viewBox="0 0 50 30"><rect x="2" y="8" width="14" height="13" rx="1" fill="currentColor"/><rect x="16" y="16" width="30" height="5" fill="currentColor"/><rect x="5" y="10" width="7" height="5" fill="#fff"/><circle cx="9" cy="24" r="4" fill="#fff" stroke="currentColor" stroke-width="2.5"/><circle cx="33" cy="24" r="4" fill="#fff" stroke="currentColor" stroke-width="2.5"/><circle cx="42" cy="24" r="4" fill="#fff" stroke="currentColor" stroke-width="2.5"/></symbol>
    <symbol id="ico-dump" viewBox="0 0 50 30"><path d="M16 4 L40 0 L46 14 L18 18 Z" fill="currentColor"/><rect x="2" y="10" width="12" height="11" fill="currentColor"/><rect x="14" y="17" width="32" height="4" fill="currentColor"/><circle cx="9" cy="24" r="4" fill="#fff" stroke="currentColor" stroke-width="2.5"/><circle cx="37" cy="24" r="4" fill="#fff" stroke="currentColor" stroke-width="2.5"/></symbol>
    <symbol id="ico-box" viewBox="0 0 50 30"><rect x="14" y="2" width="34" height="19" fill="currentColor"/><path d="M2 21 V11 L6 6 H12 V21 Z" fill="currentColor"/><circle cx="9" cy="24" r="4" fill="#fff" stroke="currentColor" stroke-width="2.5"/><circle cx="38" cy="24" r="4" fill="#fff" stroke="currentColor" stroke-width="2.5"/></symbol>
    <symbol id="ico-pickup" viewBox="0 0 50 30"><path d="M2 20 V13 H14 L18 6 H30 V13 H48 V20 Z" fill="currentColor"/><circle cx="12" cy="22" r="4" fill="#fff" stroke="currentColor" stroke-width="2.5"/><circle cx="38" cy="22" r="4" fill="#fff" stroke="currentColor" stroke-width="2.5"/></symbol>
    <symbol id="ico-cab" viewBox="0 0 50 30"><path d="M2 21 V10 L7 4 H16 V21 Z" fill="currentColor"/><rect x="16" y="16" width="30" height="4" fill="currentColor"/><circle cx="9" cy="24" r="4" fill="#fff" stroke="currentColor" stroke-width="2.5"/><circle cx="38" cy="24" r="4" fill="#fff" stroke="currentColor" stroke-width="2.5"/></symbol>
    <symbol id="ico-flatbed" viewBox="0 0 50 30"><rect x="2" y="12" width="46" height="3" fill="currentColor"/><rect x="6" y="15" width="2" height="6" fill="currentColor"/><rect x="40" y="15" width="2" height="6" fill="currentColor"/><circle cx="41" cy="22" r="2.5" fill="currentColor"/></symbol>
    <symbol id="ico-enclosed" viewBox="0 0 50 30"><path d="M10 4 L38 2 L40 18 L12 20 Z" fill="none" stroke="currentColor" stroke-width="2.5"/><path d="M18 4 V19 M26 3 V19 M33 3 V18" stroke="currentColor" stroke-width="1.5"/><circle cx="30" cy="24" r="3.5" fill="#fff" stroke="currentColor" stroke-width="2"/></symbol>
    <symbol id="ico-van" viewBox="0 0 50 30"><rect x="4" y="3" width="38" height="16" fill="currentColor"/><rect x="4" y="19" width="44" height="2" fill="currentColor"/><circle cx="12" cy="24" r="3.5" fill="#fff" stroke="currentColor" stroke-width="2"/><circle cx="36" cy="24" r="3.5" fill="#fff" stroke="currentColor" stroke-width="2"/></symbol>
    <symbol id="ico-cargo" viewBox="0 0 50 30"><path d="M4 22 V4 H34 L46 12 V22 Z" fill="currentColor"/><rect x="36" y="7" width="6" height="5" fill="#fff"/><circle cx="12" cy="24" r="4" fill="#fff" stroke="currentColor" stroke-width="2.5"/><circle cx="38" cy="24" r="4" fill="#fff" stroke="currentColor" stroke-width="2.5"/></symbol>
    <symbol id="ico-hauler" viewBox="0 0 50 30"><path d="M2 8 H44 M2 17 H48 M4 8 V17 M24 8 V17 M44 8 V17" stroke="currentColor" stroke-width="2.5" fill="none"/><circle cx="10" cy="23" r="3.5" fill="#fff" stroke="currentColor" stroke-width="2"/><circle cx="40" cy="23" r="3.5" fill="#fff" stroke="currentColor" stroke-width="2"/></symbol>
    <symbol id="ico-tow" viewBox="0 0 50 30"><path d="M2 21 V10 L7 4 H16 V21 Z" fill="currentColor"/><rect x="16" y="16" width="28" height="4" fill="currentColor"/><path d="M20 16 L40 4" stroke="currentColor" stroke-width="3"/><circle cx="9" cy="24" r="4" fill="#fff" stroke="currentColor" stroke-width="2.5"/><circle cx="36" cy="24" r="4" fill="#fff" stroke="currentColor" stroke-width="2.5"/></symbol>
  </defs>
</svg>

<div class="topbar">
  <div class="count">256, 140 Trucks and trailers For Sale</div>
  <div class="account">My Trader: &nbsp; Login &nbsp;|&nbsp; Register &nbsp;|&nbsp; Find aDealer &nbsp;|&nbsp; Dealer Login</div>
</div>

<header class="header">
  <div class="brand">Haulway Bazaar</div>
  <nav class="mainnav"><a>Find</a><a>Sell</a><a>Research</a></nav>
  <div class="social">
    <span style="background:#3b5998"></span><span style="background:#1da1f2"></span><span style="background:#dd4b39"></span><span style="background:#0e76a8"></span>
  </div>
</header>

<section class="search">
  <label>Quick Search</label>
  <div class="field" style="left:88px;width:170px">Keyword</div>
  <div class="field select" style="left:266px;width:167px">Select a Class</div>
  <div class="field select" style="left:443px;width:167px">Select a Category</div>
  <div class="field select" style="left:619px;width:167px">Select a Make</div>
  <div class="field" style="left:794px;width:93px;color:#bbb">Zip Code</div>
  <div class="field select" style="left:895px;width:111px">Any Distance</div>
  <div class="search-btn">Search</div>
</section>

<section class="category heavy" style="top:188px">
  <h2>Find Heavy Duty Trucks For Sale</h2>
  <div class="sub">What Type Heavy Duty Truck do you need?</div>
  <ul><li>Cab-Chassis</li><li>Flatbed-Truck</li><li>Box Truck-Straight Truck</li><li>Day Cab</li><li>Tractor</li><li>Crane Truck</li><li>Bucket Truck - Boom Truck</li></ul>
  <a class="see-all">See All Heavy Duty Trucks</a>
  <div class="types">
    <div class="type"><svg><use href="#ico-tractor"/></svg>Conventional<br>Sleeper Truck</div>
    <div class="type"><svg><use href="#ico-dump"/></svg>Dump<br>Truck</div>
    <div class="type"><svg><use href="#ico-tractor"/></svg>Conventional<br>Day Cab</div>
    <div class="type"><svg><use href="#ico-tow"/></svg>Conventional<br>Day Cab</div>
    <div class="hub"></div>
  </div>
</section>

<section class="category medium" style="top:534px">
  <h2>Find Medium Duty Trucks For Sale</h2>
  <div class="sub">What Type of Medium Duty Truck do you need?</div>
  <ul><li>Rollback Tow Truck</li><li>Utility Truck - Service Truck</li><li>Crew Cab</li><li>Refrigerated Truck</li><li>Wrecker Tow Truck</li><li>Bucket Truck - Boom Truck</li><li>Flatbed</li></ul>
  <a class="see-all">See All Medium Duty Trucks</a>
  <div class="types">
    <div class="type"><svg><use href="#ico-box"/></svg>Box Truck<br>Straight Truck</div>
    <div class="type"><svg><use href="#ico-dump"/></svg>Dump<br>Truck</div>
    <div class="type"><svg><use href="#ico-cab"/></svg>Cab<br>Chassis</div>
    <div class="type"><svg><use href="#ico-hauler"/></svg>Flatbed<br>Truck</div>
    <div class="hub"></div>
  </div>
</section>

<section class="category light" style="top:879px">
  <h2>Find Light Duty Trucks For Sale</h2>
  <div class="sub">What Type of Light Duty Truck do you need?</div>
  <ul><li>Dump Truck</li><li>Crew Cab</li><li>Flatbed Truck</li><li>Van</li><li>Passenger Van</li><li>Cutaway-Cube Van</li><li>Refrigerated Truck</li></ul>
  <a class="see-all">See All Light Duty Trucks</a>
  <div class="types">
    <div class="type"><svg><use href="#ico-box"/></svg>Utility truck<br>Service Truck</div>
    <div class="type"><svg><use href="#ico-pickup"/></svg>Pickup<br>Truck</div>
    <div class="type"><svg><use href="#ico-box"/></svg>Box Truck<br>Straight Truck</div>
    <div class="type"><svg><use href="#ico-cargo"/></svg>Cargo<br>Van</div>
    <div class="hub"></div>
  </div>
</section>

<section class="category trailers" style="top:1227px">
  <h2>Find Truck Trailers For Sale</h2>
  <div class="sub">What Type of Trailer do you need?</div>
  <ul><li>Dump Trailer</li><li>Lowboy Trailer</li><li>Reefer Van</li><li>Gooseneck Trailer</li><li>End Dump Trailer</li><li>Utility Trailer</li><li>Drop Deck</li></ul>
  <a class="see-all">See All Truck Trailers</a>
  <div class="types">
    <div class="type"><svg><use href="#ico-enclosed"/></svg>Enclosed<br>Trailer</div>
    <div class="type"><svg><use href="#ico-flatbed"/></svg>Flatbed<br>Trailer</div>
    <div class="type"><svg><use href="#ico-van"/></svg>Dry Van<br>Trailer</div>
    <div class="type"><svg><use href="#ico-hauler"/></svg>Car<br>Hauler</div>
    <div class="hub"></div>
  </div>
</section>

<aside class="box states" style="top:237px;height:584px">
  <h3 style="top:44px">Trucks for sale by State</h3>
  <ul class="cols" style="top:85px">
    <li>California</li><li>Lousiana</li><li>Colorado</li><li>Maine</li><li>Connecticut</li><li>Maryland</li><li>Delaware</li><li>Masachusetts</li><li>Florida</li><li>Michigan</li><li>Georgia</li><li>Minnesota</li><li>Hawaii</li><li>Mississippi</li><li>Idaho</li><li>Missouri</li><li>Illinois</li><li>Montana</li>
  </ul>
  <div class="divider" style="top:291px"></div>
  <ul class="cols" style="top:305px">
    <li>Nebraska</li><li>Rhode Island</li><li>Nevada</li><li>South Carolina</li><li>New Hampshire</li><li>South Dakota</li><li>New Jersey</li><li>Tennessee</li><li>New Mexico</li><li>Texas</li><li>New York</li><li>Utah</li><li>North Carolina</li><li>Vermont</li><li>North Dakota</li><li>Virginia</li><li>Ohio</li><li>Washington</li><li>Oklahoma</li><li>West Virginia</li><li>Oregon</li><li>Wisconsin</li><li>Pennsylvania</li><li>Wyoming</li>
  </ul>
</aside>

<aside class="box makes" style="top:845px;height:255px">
  <h3 style="top:22px">Trucks for sale by Make</h3>
  <ul class="cols" style="top:47px">
    <li>Ironvale</li><li>Meridian</li><li>Haulstar</li><li>Kestrel</li><li>Brightway</li><li>Granite</li><li>Pinecrest</li><li>Ventor</li>
  </ul>
  <div class="divider" style="top:142px"></div>
  <ul class="cols" style="top:156px">
    <li>Kaito</li><li>Hayato</li><li>Bastion</li><li>Silverton</li><li>Nordvik</li><li>Altenberg</li><li>Redline</li><li>Tomoe</li>
  </ul>
</aside>

<div class="ad" role="img" aria-label="Advertisement banner: semi truck at dusk">AD 133x199</div>

<aside class="box dealer" style="top:1331px;height:214px">
  <h3>Find a Dealer</h3>
  <p>Find Commercial Truck dealers by name,make and location.</p>
  <a class="btn">Find a Dealer</a>
  <div class="map" role="img" aria-label="Dotted world map with a location pin" style="background:radial-gradient(ellipse at 50% 55%,#d6d6d6 0%,#ececec 60%,#fff 100%)">
    <svg viewBox="0 0 130 76" width="130" height="76"><path d="M72 4 a9 9 0 0 1 9 9 c0 7 -9 17 -9 17 s-9 -10 -9 -17 a9 9 0 0 1 9 -9z" fill="var(--orange)"/><circle cx="72" cy="13" r="3.5" fill="#fff"/></svg>
  </div>
</aside>

<div class="featured-title">
  <h2>Featured Ads</h2>
  <p>View all photo featured trucks and trailers for sale &nbsp;|&nbsp; Place your listing here</p>
  <hr>
</div>

<article class="card" style="left:88px">
  <div class="photo" role="img" aria-label="Red light duty pickup truck" style="background:linear-gradient(180deg,#f1b35a 0%,#c9553a 55%,#5a4a44 100%)"></div>
  <h4>Light Duty</h4><div class="model">2017 Ironvale R-350</div>
  <ul><li>Cab Cassis, Flatbed Truck</li><li>$63, 345.00</li><li>New Braunfels, TX</li></ul>
</article>
<article class="card" style="left:350px">
  <div class="photo" role="img" aria-label="Red medium duty cab chassis truck" style="background:linear-gradient(180deg,#c9d3dc 0%,#b84a44 55%,#6d5e52 100%)"></div>
  <h4>Medium Duty</h4><div class="model">2016 KAITO KR4</div>
  <ul><li>Pickup Truck</li><li>$34,844.00</li><li>Cleveland, OH</li></ul>
</article>
<article class="card" style="left:611px">
  <div class="photo" role="img" aria-label="Dark heavy duty semi truck" style="background:linear-gradient(180deg,#dfe3e6 0%,#5a6068 55%,#3a3c40 100%)"></div>
  <h4>Heavy Duty</h4><div class="model">2016 IRONVALE R750</div>
  <ul><li>Dump Truck, Landscape Truck</li><li>$76,500.00</li><li>Whittier, CA</li></ul>
</article>
<article class="card" style="left:871px">
  <div class="photo" role="img" aria-label="Truck hauling a red container trailer" style="background:linear-gradient(180deg,#8aa4c8 0%,#9a5a4c 55%,#8c8a86 100%)"></div>
  <h4>Trailer</h4><div class="model">2012 Deckmaster DL2100</div>
  <ul><li>Other Trailer</li><li>$42,000.00</li><li>Pearl City, IL</li></ul>
</article>

<a class="all-featured">View all featured trucks and trailers for sale</a>

<footer class="footer">
  <h3 style="left:88px">Commercial Truck Blog</h3>
  <div class="post" style="top:75px">
    <div class="thumb" role="img" aria-label="Blog photo of a truck"></div>
    <div class="body"><div>Lorem ipsum dolor sit amet.</div><div class="date">&#9632; 24th November</div><div class="text">Lorem ipsum dolor sit amet, consectetur<br>adipiscing elit, sed do eiusmod.</div></div>
  </div>
  <div class="post" style="top:169px">
    <div class="thumb" role="img" aria-label="Blog photo of a truck"></div>
    <div class="body"><div>Lorem ipsum dolor sit amet.</div><div class="date">&#9632; 24th November</div><div class="text">Lorem ipsum dolor sit amet, consectetur<br>adipiscing elit, sed do eiusmod.</div></div>
  </div>

  <h3 style="left:433px">Chirpline Feed</h3>
  <div class="tweet" style="top:75px">
    <div class="icon"></div>
    <div class="body"><div>Lorem ipsum dolor sit amet.</div><div class="text">Lorem ipsum dolor sit amet, consectetur<br>adipiscing elit, sed do eiusmod.</div></div>
    <div class="actions">&#8635; Repost <span class="fav">&#9733; Favorite</span></div>
  </div>
  <div class="tweet" style="top:169px">
    <div class="icon"></div>
    <div class="body"><div>Lorem ipsum dolor sit amet.</div><div class="text">Lorem ipsum dolor sit amet, consectetur<br>adipiscing elit, sed do eiusmod.</div></div>
    <div class="actions">&#8635; Repost <span class="fav hot">&#9733; Favorite</span></div>
  </div>

  <h3 style="left:845px;top:45px">Quick Links</h3>
  <div class="links">
    <a>Insurance</a><a>Truck Parts</a><a>Jobs &amp; Training</a><a>Steel Buildings</a><a>Vehicle History</a><a>Fuel Management</a><a>Truck Bodies</a><a>Shipping &amp; Transport</a><a>Finance/Lease</a>
  </div>
</footer>
<div class="bottombar">Copyright 2016 &nbsp;All Rights Reserved</div>

</body>
</html>
```